Business Card Design

New business card design

Target Market(s)

Residential & Commercial Property Managers

Industry/Entity Type

Plumbing Services

Contact Information for Business Card

Name - Rowan Keddle, title - Director, Phone Number - 0431 286 517, email - rowan@tbk-plumbing.com.au, Company ABN - 73 215 904 386,

Font styles to use
Sans Serif

Colors
0054AA
0677BA
7BADD7
CADEEF
E8F1F8

```html
<!DOCTYPE html>
<html lang="en">
<head>
<meta charset="utf-8">
<title>TBK Plumbing Services – Business Card</title>
<link rel="stylesheet" href="https://fonts.googleapis.com/css2?family=Poppins:wght@300;400;500;600&display=swap">
<style>
  :root {
    --backdrop: #222222;
    --card: #ffffff;
    --ink: #1b232b;
    --taupe: #7a6e64;
    --blue: #29a9e1;
  }
  * { box-sizing: border-box; margin: 0; padding: 0; }
  html, body {
    width: 1200px; height: 711px; overflow: hidden;
    background: var(--backdrop);
    font-family: "Poppins", sans-serif;
  }
  .stage {
    width: 1200px; height: 711px;
    display: flex; align-items: center; justify-content: center; gap: 44px;
  }
  .card {
    position: relative;
    width: 540px; height: 309px;
    background: var(--card);
    border-bottom: 7px solid var(--blue);
    box-shadow: 0 14px 30px rgba(0,0,0,.55);
    overflow: hidden;
  }

  /* company name placeholder: one colour, one weight */
  .company-name {
    color: var(--ink);
    font-weight: 500;
    line-height: 1.2;
    white-space: nowrap;
  }

  /* front */
  .card-front { display: flex; align-items: center; justify-content: center; }
  .card-front .company-name { font-size: 38px; }

  /* back */
  .card-back .company-name {
    position: absolute; left: 0; top: 132px; width: 268px;
    text-align: center; font-size: 18px;
  }

  .divider {
    position: absolute; left: 268px; top: 62px;
    width: 1.5px; height: 150px; background: var(--blue);
  }
  .contact { position: absolute; left: 292px; top: 64px; }
  .person-name { font-size: 25px; line-height: 1.1; font-weight: 400; }
  .first-name { color: var(--blue); font-weight: 600; }
  .last-name { color: var(--taupe); font-weight: 300; }
  .person-title { font-size: 12px; font-weight: 500; color: var(--ink); margin: 2px 0 16px 6px; }
  .contact-list { list-style: none; }
  .contact-item {
    display: flex; align-items: center; gap: 9px;
    font-size: 11.5px; color: var(--ink); line-height: 21px;
  }
  .contact-item svg { width: 13px; height: 13px; flex: none; }
  .abn {
    position: absolute; left: 292px; bottom: 22px;
    font-size: 12px; color: var(--blue); letter-spacing: .3px;
  }
</style>
</head>
<body>
<main class="stage">

  <section class="card card-front" aria-label="Card front">
    <p class="company-name">TBK Plumbing Services</p>
  </section>

  <section class="card card-back" aria-label="Card back">
    <p class="company-name">TBK Plumbing Services</p>

    <div class="divider"></div>

    <div class="contact">
      <h1 class="person-name"><span class="first-name">Rowan</span> <span class="last-name">Keddle</span></h1>
      <p class="person-title">Director</p>
      <ul class="contact-list">
        <li class="contact-item">
          <svg viewBox="0 0 24 24" aria-hidden="true"><path fill="#29a9e1" d="M6.6 10.8a15.1 15.1 0 0 0 6.6 6.6l2.2-2.2a1 1 0 0 1 1-.25 11.4 11.4 0 0 0 3.6.57 1 1 0 0 1 1 1V20a1 1 0 0 1-1 1A17 17 0 0 1 3 4a1 1 0 0 1 1-1h3.5a1 1 0 0 1 1 1c0 1.25.2 2.45.57 3.57a1 1 0 0 1-.25 1z"/></svg>
          0431 286 517
        </li>
        <li class="contact-item">
          <svg viewBox="0 0 24 24" aria-hidden="true"><rect x="2" y="5" width="20" height="14" rx="1.5" fill="#29a9e1"/><path d="M3 6.5l9 6.5 9-6.5" fill="none" stroke="#fff" stroke-width="1.6"/></svg>
          www.tbk-plumbing.com.au
        </li>
        <li class="contact-item">
          <svg viewBox="0 0 24 24" aria-hidden="true"><circle cx="12" cy="12" r="9" fill="none" stroke="#29a9e1" stroke-width="2"/><path d="M3 12h18M12 3c3 3 3 15 0 18M12 3c-3 3-3 15 0 18" fill="none" stroke="#29a9e1" stroke-width="1.6"/></svg>
          rowan@tbk-plumbing.com.au
        </li>
      </ul>
    </div>

    <p class="abn">ABN - 73 215 904 386</p>
  </section>

</main>
</body>
</html>
```